Infographic for a Life Transformation brand to showcase their principle method

I need a clean infographic which would be used in a brochure to show the 5 steps to achieving a Keystone Uprising. (ie Life transformation). I use the theme of a revolution so I would like the graphic to include a raised fist or something to represent a revolution and then the 5 points of information to represent each step.
Needs to very clean and simple. I don't want something that would take up a full page, I want it as a graphic, almost like a big logo. I don't want it laid out like a process chart.

My brand personalities from https://voxelmarquee.com.au/ are
The Everyman and The Magician to give you an idea of my brand.

I've attached my logo so that you can see the colour of it. Graphic doesn't need to match logo but should align with that colour.

Target Market(s)

Top Tier Executives, males, 35-55y old

Industry/Entity Type

Life Coaching

Requirements
Must have
• The graphic must have the 5 Steps: in this order
1.Clarity
2. Measurement
3. Discipline
4. Nutrition
5.Exercise
Nice to have
• It could include these action steps which line up with the 5 steps, It may be too much information by there is the option to include if it works.
1.see it
2. track it
3. do it
4. eat it
5. move it

```html
<!DOCTYPE html>
<html lang="en">
<head>
<meta charset="utf-8">
<title>Keystone Uprising – Five Steps</title>
<link rel="stylesheet" href="https://fonts.googleapis.com/css2?family=Montserrat:wght@500;600;700&display=swap">
<style>
  :root {
    --brand-blue: #1b4f95;
    --brand-red: #c1413b;
    --ring-grey: #d6d6d8;
    --paper: #ffffff;
  }
  html, body {
    margin: 0;
    padding: 0;
    width: 1200px;
    height: 1200px;
    overflow: hidden;
    background: var(--paper);
  }
  .poster {
    position: relative;
    width: 1200px;
    height: 1200px;
    font-family: "Montserrat", sans-serif;
  }
  .brand {
    position: absolute;
    top: 96px;
    left: 0;
    width: 100%;
    display: flex;
    justify-content: center;
    align-items: center;
    gap: 16px;
  }
  .brand-mark {
    width: 22px;
    height: 22px;
    background: var(--brand-blue);
  }
  .brand-name {
    margin: 0;
    font-size: 26px;
    font-weight: 600;
    letter-spacing: 4px;
    color: var(--brand-blue);
  }
  .method-wheel {
    position: absolute;
    top: 0;
    left: 0;
  }
  .step-label {
    font-family: "Montserrat", sans-serif;
    font-weight: 600;
    font-size: 23px;
    letter-spacing: 1px;
    fill: #ffffff;
  }
  .action-label {
    font-family: "Montserrat", sans-serif;
    font-weight: 700;
    font-size: 21px;
    letter-spacing: 1px;
    fill: var(--brand-red);
  }
  .icon {
    fill: none;
    stroke: var(--brand-blue);
    stroke-width: 3;
    stroke-linecap: round;
    stroke-linejoin: round;
  }
  .footer-band {
    position: absolute;
    left: 0;
    bottom: 0;
    width: 100%;
    height: 38px;
    background: var(--brand-blue);
  }
</style>
</head>
<body>
<main class="poster">
  <header class="brand">
    <span class="brand-mark"></span>
    <h1 class="brand-name">KEYSTONE UPRISING</h1>
  </header>

  <svg class="method-wheel" width="1200" height="1200" viewBox="0 0 1200 1200">
    <defs>
      <path id="outer-track" d="M600,258 A380,380 0 1 1 600,1018 A380,380 0 1 1 600,258"/>
      <path id="inner-track" d="M600,311 A327,327 0 1 1 600,965 A327,327 0 1 1 600,311"/>
    </defs>

    <!-- rings -->
    <circle cx="600" cy="638" r="410" fill="var(--brand-blue)"/>
    <circle cx="600" cy="638" r="360" fill="var(--ring-grey)"/>
    <circle cx="600" cy="638" r="360" fill="none" stroke="#ffffff" stroke-width="5"/>

    <!-- sunburst segments -->
    <g class="segments" fill="var(--brand-red)">
      <path d="M600,638 L310.7,737.6 A306,306 0 0 1 294.2,627.3 Z"/>
      <path d="M600,638 L329.8,494.3 A306,306 0 0 1 395.3,410.6 Z"/>
      <path d="M600,638 L515.7,343.8 A306,306 0 0 1 621.4,332.7 Z"/>
      <path d="M600,638 L753,373 A306,306 0 0 1 847.6,458.1 Z"/>
      <path d="M600,638 L901.3,584.9 A306,306 0 0 1 383.6,854.4 Z"/>
    </g>
    <circle cx="600" cy="638" r="308" fill="none" stroke="#ffffff" stroke-width="4"/>

    <!-- step names on the blue ring -->
    <text class="step-label" text-anchor="middle"><textPath href="#outer-track" startOffset="66%">CLARITY</textPath></text>
    <text class="step-label" text-anchor="middle"><textPath href="#outer-track" startOffset="80%">MEASUREMENT</textPath></text>
    <text class="step-label" text-anchor="middle"><textPath href="#outer-track" startOffset="92.5%">DISCIPLINE</textPath></text>
    <text class="step-label" text-anchor="middle"><textPath href="#outer-track" startOffset="5%">NUTRITION</textPath></text>
    <text class="step-label" text-anchor="middle"><textPath href="#outer-track" startOffset="18.3%">EXERCISE</textPath></text>

    <!-- direction arrows -->
    <g fill="#ffffff">
      <path d="M-7,-8 L8,0 L-7,8 Z" transform="translate(220,726) rotate(-13)"/>
      <path d="M-7,-8 L8,0 L-7,8 Z" transform="translate(290,405) rotate(-53)"/>
      <path d="M-7,-8 L8,0 L-7,8 Z" transform="translate(561,261) rotate(-6)"/>
      <path d="M-7,-8 L8,0 L-7,8 Z" transform="translate(845,345) rotate(40)"/>
    </g>

    <!-- action phrases on the grey ring -->
    <text class="action-label" text-anchor="middle"><textPath href="#inner-track" startOffset="65.8%">SEE IT</textPath></text>
    <text class="action-label" text-anchor="middle"><textPath href="#inner-track" startOffset="79.2%">TRACK IT</textPath></text>
    <text class="action-label" text-anchor="middle"><textPath href="#inner-track" startOffset="94.4%">DO IT</textPath></text>
    <text class="action-label" text-anchor="middle"><textPath href="#inner-track" startOffset="3.6%">EAT IT</textPath></text>
    <text class="action-label" text-anchor="middle"><textPath href="#inner-track" startOffset="16.7%">MOVE IT</textPath></text>

    <!-- step icons -->
    <g class="icon" transform="translate(347,750)">
      <path d="M4,28 Q28,6 52,28 Q28,50 4,28 Z"/>
      <circle cx="28" cy="28" r="8"/>
      <circle cx="28" cy="28" r="2.5"/>
    </g>
    <g class="icon" transform="translate(316,541)">
      <circle cx="22" cy="26" r="16"/>
      <circle cx="22" cy="26" r="5"/>
      <path d="M22,42 H54 V30 H38"/>
      <path d="M44,42 V37 M50,42 V37"/>
    </g>
    <g class="icon" transform="translate(443,378)">
      <rect x="10" y="8" width="36" height="44" rx="3"/>
      <rect x="20" y="4" width="16" height="8" rx="2"/>
      <path d="M16,22 l3,3 l5,-5 M28,23 H40 M16,33 l3,3 l5,-5 M28,34 H40 M16,44 l3,3 l5,-5 M28,45 H40"/>
    </g>
    <g class="icon" transform="translate(649,357)">
      <path d="M6,30 H50 Q48,48 28,48 Q8,48 6,30 Z"/>
      <path d="M20,48 V52 H36 V48"/>
      <circle cx="20" cy="22" r="6"/>
      <circle cx="34" cy="18" r="5"/>
      <path d="M42,26 L52,10"/>
    </g>
    <g class="icon" transform="translate(816,506)">
      <path d="M10,42 L22,14 L32,18 Q34,30 48,34 Q54,36 52,44 H10 Z"/>
      <path d="M10,48 H52"/>
      <path d="M2,22 H10 M0,30 H8"/>
    </g>

    <!-- central emblem area -->
    <path d="M440,450 H750 Q790,450 790,490 V790 L730,850 V990 H470 V850 L400,790 V490 Q400,450 440,450 Z"
          fill="var(--brand-blue)" stroke="#ffffff" stroke-width="6"
          role="img" aria-label="Raised clenched fist illustration, symbol of revolution"/>
  </svg>

  <div class="footer-band"></div>
</main>
</body>
</html>
```